Maple9Tone

I need a website designed to feature a new product for my company. I am dedicating a separate site just highlight the program. The url will be maple9tone.com and the product name is maple tone. The product is ringless voicemail. We take a recorded script and send it to our clients customers cell phones without the phone ringing.

The site will consist of a home page. I animated video demo. It will house 18 scripts and voice overs to match, a results page, and a page to request a live demo.

We sell the product to new car dealerships

```html
<!DOCTYPE html>
<html lang="en">
<head>
<meta charset="utf-8">
<title>Maple Tone – Ringless Voicemail</title>
<link href="https://fonts.googleapis.com/css2?family=Jost:wght@400;500&family=Open+Sans:wght@400;600;700&family=Roboto+Condensed:wght@400&display=swap" rel="stylesheet">
<style>
:root{
  --orange:#f47a20;
  --orange-dark:#e8651a;
  --blue:#0a6fc2;
  --ink:#222;
  --text:#555;
  --grey-bg:#f4f4f4;
  --tile:#efefef;
  --line:#d8d8d8;
  --hero:#4a4a4a;
  --white:#fff;
}
*{box-sizing:border-box;margin:0;padding:0}
html,body{width:1200px;height:2590px;overflow:hidden;background:var(--white)}
body{position:relative;font-family:"Open Sans",Arial,sans-serif;color:var(--ink)}
.abs{position:absolute}

/* header */
.site-header{position:absolute;left:0;top:0;width:1200px;height:137px;background:var(--white)}
.brand{position:absolute;left:74px;top:38px;display:flex;align-items:center;gap:12px}
.brand-mark{width:40px;height:40px;border:3px solid var(--blue)}
.brand-name{font-family:"Jost",sans-serif;font-size:34px;font-weight:400;color:var(--blue);line-height:1}
.call{position:absolute;right:74px;top:22px;font-size:14px;font-weight:600;color:var(--ink)}
.call strong{font-size:22px;color:var(--blue);font-weight:600;margin-left:6px}
.main-nav{position:absolute;right:74px;top:76px;display:flex;gap:0;align-items:center}
.main-nav a{font-size:14px;font-weight:600;color:var(--ink);text-decoration:none;padding:6px 22px;margin-left:4px;border:2px solid transparent;border-radius:18px}
.main-nav a.active{border-color:var(--orange);color:var(--orange)}
.main-nav a:last-child{padding-right:0}

/* hero */
.hero{position:absolute;left:0;top:137px;width:1200px;height:504px;background:radial-gradient(ellipse at 55% 45%,#6a6a6a 0%,var(--hero) 55%,#333 100%)}
.play{position:absolute;left:552px;top:203px;width:96px;height:96px;border-radius:50%;background:var(--white)}
.play svg{position:absolute;left:33px;top:27px}

/* section headings */
.section-title{position:absolute;left:0;width:1200px;text-align:center;font-family:"Jost",sans-serif;font-weight:400;font-size:27px;letter-spacing:.5px;color:var(--ink)}

/* features */
.features{position:absolute;left:74px;top:780px;display:flex;gap:27px}
.feature{width:242px;height:78px;background:var(--tile);display:flex;align-items:center;justify-content:center;gap:16px;font-size:21px;color:var(--ink)}
.feature.active{background:var(--blue);color:var(--white)}
.feature .dollar{font-size:36px;font-weight:700}
.feature .two-line{font-size:20px;line-height:1.15}

/* how it works */
.how{position:absolute;left:0;top:922px;width:1200px;height:670px;background:var(--grey-bg)}
.step{position:absolute;width:202px;height:202px;border-radius:50%;background:var(--orange);border:5px solid var(--white);box-shadow:0 2px 8px rgba(0,0,0,.18);display:flex;align-items:center;justify-content:center;text-align:center;padding:0 32px;font-family:"Roboto Condensed",sans-serif;font-size:16px;line-height:1.3;color:var(--white)}
.flow-arrow{position:absolute}

/* offer */
.offer-title{position:absolute;left:74px;top:1668px;font-family:"Jost",sans-serif;font-size:27px;color:var(--ink)}
.offer-list{position:absolute;left:74px;top:1736px;width:580px;list-style:none}
.offer-list li{position:relative;padding-left:34px;font-size:11.5px;line-height:1.65;color:var(--text);text-transform:uppercase;margin-bottom:14px}
.offer-photo{position:absolute;left:704px;top:1661px;width:422px;height:261px;background:linear-gradient(135deg,#d9d4ce 0%,#b7a89a 50%,#8e7d70 100%)}

/* scripts */
.scripts{position:absolute;left:0;top:1984px;width:1200px;height:318px;background:var(--grey-bg)}
.script-col{position:absolute;top:2114px;list-style:none}
.script-col li{position:relative;padding-left:30px;font-size:14px;color:var(--text);height:33px}
.bullet{position:absolute;left:0;top:3px}

/* partners */
.partners{position:absolute;left:74px;top:2345px;width:1052px;height:107px;border-top:1px solid var(--line);border-bottom:1px solid var(--line);display:flex;align-items:center;justify-content:space-between;padding:0 50px}
.partner{display:flex;align-items:center;gap:10px;font-size:22px;font-weight:700;color:#444}
.partner-dot{width:22px;height:22px;border-radius:50%;background:#888}

/* footer */
.site-footer{position:absolute;left:0;top:2492px;width:1200px;height:98px;background:var(--grey-bg)}
.copyright{position:absolute;left:74px;top:45px;font-size:13px;font-weight:700;color:var(--ink)}
.social{position:absolute;right:74px;top:34px;display:flex;gap:8px}
.social span{width:32px;height:32px;border-radius:50%}
</style>
</head>
<body>

<header class="site-header">
  <div class="brand"><span class="brand-mark"></span><span class="brand-name">Harlow Outreach</span></div>
  <div class="call">Call us today at <strong>555 014 2290</strong></div>
  <nav class="main-nav">
    <a class="active" href="#">HOME</a>
    <a href="#">HOW IT WORK</a>
    <a href="#">THE OFFER</a>
    <a href="#">AVAILABLE</a>
    <a href="#">SCRIPTS</a>
    <a href="#">CONTACT</a>
  </nav>
</header>

<section class="hero" role="img" aria-label="Video still: hands sketching a marketing plan with doodled icons on paper">
  <div class="play"><svg width="36" height="42" viewBox="0 0 36 42"><path d="M0 0 L36 21 L0 42 Z" fill="#333"/></svg></div>
</section>

<h2 class="section-title" style="top:710px">MAPLE TONE</h2>
<div class="features">
  <div class="feature active">
    <svg width="44" height="40" viewBox="0 0 44 40" fill="none" stroke="#fff" stroke-width="3"><circle cx="26" cy="22" r="14"/><path d="M26 22 L32 16 M22 4 H30 M26 4 V8"/><path d="M2 16 H10 M0 22 H9 M3 28 H10" stroke-linecap="round"/></svg>
    <span>Fast</span>
  </div>
  <div class="feature">
    <svg width="44" height="44" viewBox="0 0 44 44" fill="none" stroke="#222" stroke-width="3"><circle cx="20" cy="24" r="16"/><circle cx="20" cy="24" r="9"/><circle cx="20" cy="24" r="3" fill="#222"/><path d="M20 24 L38 6 M32 4 L38 6 L40 12"/></svg>
    <span>Effective</span>
  </div>
  <div class="feature"><span class="dollar">$</span><span>Inexpensive</span></div>
  <div class="feature">
    <svg width="44" height="40" viewBox="0 0 44 40" fill="#222"><path d="M4 14 H12 L32 4 V34 L12 24 H4 Z"/><rect x="10" y="24" width="6" height="12"/><path d="M36 12 L42 8 M36 19 H43 M36 26 L42 30" stroke="#222" stroke-width="3"/></svg>
    <span class="two-line">Versatile<br>Marketing</span>
  </div>
</div>

<section class="how">
  <h2 class="section-title" style="top:68px">HOW IT WORKS</h2>
</section>
<svg class="abs" style="left:0;top:0" width="1200" height="1600">
  <g fill="#bbb">
    <path d="M318 1163 L330 1171 L318 1179 L318 1174 L308 1174 L308 1168 L318 1168 Z"/>
    <path d="M590 1163 L602 1171 L590 1179 L590 1174 L580 1174 L580 1168 L590 1168 Z"/>
    <path d="M862 1163 L874 1171 L862 1179 L862 1174 L852 1174 L852 1168 L862 1168 Z"/>
    <path d="M318 1417 L330 1425 L318 1433 L318 1428 L308 1428 L308 1422 L318 1422 Z"/>
    <path d="M590 1417 L602 1425 L590 1433 L590 1428 L580 1428 L580 1422 L590 1422 Z"/>
    <path d="M862 1417 L874 1425 L862 1433 L862 1428 L852 1428 L852 1422 L862 1422 Z"/>
  </g>
  <path d="M1007 1272 V1290 H195 V1312" fill="none" stroke="#ccc" stroke-width="3"/>
  <path d="M187 1308 L195 1318 L203 1308" fill="none" stroke="#ccc" stroke-width="3"/>
</svg>
<div class="step" style="left:92px;top:1070px">We select a targeted list of past sales customers, service customers, or unsold leads.</div>
<div class="step" style="left:364px;top:1070px">We develop and record a script based on your stores current needs, incentives, time of year, and list.</div>
<div class="step" style="left:635px;top:1070px">Your team will be coached and given a set of scripted responses to be sure everyone is prepared.</div>
<div class="step" style="left:906px;top:1070px">Your message and list are uploaded to our system and delivered at any speed you wish.</div>
<div class="step" style="left:92px;top:1324px">Inbound return calls will begin within minutes.</div>
<div class="step" style="left:364px;top:1324px">This program requires zero set up.</div>
<div class="step" style="left:635px;top:1324px">The simple process above can be completed and go live in as little as 24 hours.</div>
<div class="step" style="left:906px;top:1324px">Every inbound phone call is recorded, tracked, and caller id information is captured.</div>

<h2 class="offer-title">THE OFFER</h2>
<ul class="offer-list">
  <li><svg class="bullet" width="14" height="14" viewBox="0 0 14 14"><path d="M0 6 H9 V2 L14 7 L9 12 V8 H0 Z" fill="#f47a20"/></svg>We can use this as a buy back offer, re-engage unsold CRM leads, offer monthly factory incentives, inform of a sales event, or to get CSI surveys completed</li>
  <li><svg class="bullet" width="14" height="14" viewBox="0 0 14 14"><path d="M0 6 H9 V2 L14 7 L9 12 V8 H0 Z" fill="#f47a20"/></svg>It can be recorded by anyone!</li>
  <li><svg class="bullet" width="14" height="14" viewBox="0 0 14 14"><path d="M0 6 H9 V2 L14 7 L9 12 V8 H0 Z" fill="#f47a20"/></svg>Works because the message is perfect every time!</li>
  <li><svg class="bullet" width="14" height="14" viewBox="0 0 14 14"><path d="M0 6 H9 V2 L14 7 L9 12 V8 H0 Z" fill="#f47a20"/></svg>The information stays with them!</li>
</ul>
<div class="offer-photo" role="img" aria-label="Photo: hands in a knit sweater holding a small gift wrapped with twine"></div>

<section class="scripts">
  <h2 class="section-title" style="top:65px">AVAILABLE SCRIPTS</h2>
</section>
<ul class="script-col" style="left:74px">
  <li><svg class="bullet" width="14" height="14" viewBox="0 0 14 14"><path d="M0 6 H9 V2 L14 7 L9 12 V8 H0 Z" fill="#f47a20"/></svg>January- New Years</li>
  <li><svg class="bullet" width="14" height="14" viewBox="0 0 14 14"><path d="M0 6 H9 V2 L14 7 L9 12 V8 H0 Z" fill="#f47a20"/></svg>February- Winter Special</li>
  <li><svg class="bullet" width="14" height="14" viewBox="0 0 14 14"><path d="M0 6 H9 V2 L14 7 L9 12 V8 H0 Z" fill="#f47a20"/></svg>March- Spring Forward</li>
  <li><svg class="bullet" width="14" height="14" viewBox="0 0 14 14"><path d="M0 6 H9 V2 L14 7 L9 12 V8 H0 Z" fill="#f47a20"/></svg>April- Tax Time</li>
</ul>
<ul class="script-col" style="left:436px">
  <li><svg class="bullet" width="14" height="14" viewBox="0 0 14 14"><path d="M0 6 H9 V2 L14 7 L9 12 V8 H0 Z" fill="#f47a20"/></svg>May- Memorial Day</li>
  <li><svg class="bullet" width="14" height="14" viewBox="0 0 14 14"><path d="M0 6 H9 V2 L14 7 L9 12 V8 H0 Z" fill="#f47a20"/></svg>June- Summer Saving</li>
  <li><svg class="bullet" width="14" height="14" viewBox="0 0 14 14"><path d="M0 6 H9 V2 L14 7 L9 12 V8 H0 Z" fill="#f47a20"/></svg>July- Independence Day</li>
  <li><svg class="bullet" width="14" height="14" viewBox="0 0 14 14"><path d="M0 6 H9 V2 L14 7 L9 12 V8 H0 Z" fill="#f47a20"/></svg>August- Back To School/Model Year End</li>
</ul>
<ul class="script-col" style="left:848px">
  <li><svg class="bullet" width="14" height="14" viewBox="0 0 14 14"><path d="M0 6 H9 V2 L14 7 L9 12 V8 H0 Z" fill="#f47a20"/></svg>September- Labor Day</li>
  <li><svg class="bullet" width="14" height="14" viewBox="0 0 14 14"><path d="M0 6 H9 V2 L14 7 L9 12 V8 H0 Z" fill="#f47a20"/></svg>October- Fall Into Savings</li>
  <li><svg class="bullet" width="14" height="14" viewBox="0 0 14 14"><path d="M0 6 H9 V2 L14 7 L9 12 V8 H0 Z" fill="#f47a20"/></svg>November- Giving Thanks/Black Friday</li>
  <li><svg class="bullet" width="14" height="14" viewBox="0 0 14 14"><path d="M0 6 H9 V2 L14 7 L9 12 V8 H0 Z" fill="#f47a20"/></svg>December- Happy Holidays/Year End</li>
</ul>

<div class="partners">
  <span class="partner">Ridgeway Motors</span>
  <span class="partner">Belmont Auto</span>
  <span class="partner"><span class="partner-dot"></span>Lumen Ads</span>
  <span class="partner">Crestline Cars</span>
</div>

<footer class="site-footer">
  <p class="copyright">COPYRIGHT © 2016 | PRIVACY POLICY</p>
  <div class="social" aria-label="Social links">
    <span style="background:#2a5ca8"></span>
    <span style="background:#3aa0dc"></span>
    <span style="background:#f29a2e"></span>
    <span style="background:#d8473a"></span>
  </div>
</footer>

</body>
</html>
```